Business Book - Building Calm Mornings at the Office (Hand Off the Small Stuff and Keep the Spark)

I'm looking for a cover that appeals to successful business people who are used to reading business titles.

The cover should feel familiar and fit in with the existing canon of bestselling business books with a vibrant, but professional look (see attached).

I want my book to stand out, but not to be frivolous. Abstract is probably best. Or close to it.

Please feel free to use my brand colours, or go with something else -

Teal
HEX #199BAB
25 / 155 / 171

Coral
HEX #EE786E
238 / 120/ 110

I don't want to include anything connected with robots or gendered assistants/business people. Or headsets.

It's only 24 hours which is mental

```html
<!DOCTYPE html>
<html lang="en">
<head>
<meta charset="utf-8">
<title>Building Calm Mornings at the Office – Cover</title>
<link rel="stylesheet" href="https://fonts.googleapis.com/css2?family=Bebas+Neue&family=Exo+2:wght@400&family=Michroma&display=swap">
<style>
  :root {
    --stage: #474747;
    --coral: #ee786e;
    --coral-light: #f39a92;
    --white: #ffffff;
    --ink: #000000;
  }
  * { margin: 0; padding: 0; box-sizing: border-box; }
  html, body {
    width: 1200px;
    height: 1077px;
    overflow: hidden;
    background: var(--stage);
  }
  .cover {
    position: absolute;
    left: 268px;
    top: 41px;
    width: 663px;
    height: 994px;
    background: var(--coral);
    box-shadow: 0 0 40px rgba(0,0,0,0.35);
    overflow: hidden;
  }
  .cover__emblem {
    position: absolute;
    left: 250px;
    top: 46px;
    width: 162px;
    height: 180px;
  }
  .cover__oval {
    position: absolute;
    left: 47px;
    top: 244px;
    width: 569px;
    height: 625px;
    background: var(--white);
    border-radius: 50%;
  }
  .title {
    position: absolute;
    left: 47px;
    top: 290px;
    width: 569px;
    height: 520px;
    display: flex;
    flex-direction: column;
    align-items: center;
    justify-content: center;
    text-align: center;
  }
  .title__quiet {
    font-family: "Exo 2", sans-serif;
    font-weight: 400;
    font-size: 62px;
    line-height: 1.05;
    color: var(--ink);
    letter-spacing: -1px;
  }
  .title__loud {
    font-family: "Bebas Neue", "Oswald", sans-serif;
    color: var(--coral);
    line-height: 0.88;
    letter-spacing: 0;
  }
  .title__loud--mid { font-size: 92px; margin: 6px 0 2px; }
  .title__loud--big { font-size: 200px; margin-top: 4px; }
  .subtitle {
    position: absolute;
    left: 47px;
    top: 752px;
    width: 569px;
    text-align: center;
    font-family: "Michroma", sans-serif;
    font-size: 17px;
    line-height: 25px;
    letter-spacing: 1.5px;
    color: var(--ink);
  }
  .author {
    position: absolute;
    left: 0;
    top: 893px;
    width: 663px;
    text-align: center;
    font-family: "Michroma", sans-serif;
    font-size: 40px;
    letter-spacing: 4px;
    color: var(--white);
  }
</style>
</head>
<body>
  <div class="cover">
    <svg class="cover__emblem" viewBox="0 0 162 180" role="img" aria-label="Small line-art emblem above the title">
      <circle cx="81" cy="98" r="80" fill="var(--coral-light)"/>
    </svg>
    <div class="cover__oval"></div>
    <h1 class="title">
      <span class="title__quiet">BUILDING</span>
      <span class="title__loud title__loud--mid">CALM MORNINGS</span>
      <span class="title__quiet">AT THE</span>
      <span class="title__loud title__loud--big">OFFICE</span>
    </h1>
    <p class="subtitle">HAND OFF THE SMALL STUFF<br>AND KEEP THE SPARK</p>
    <p class="author">AUTHOR NAME</p>
  </div>
</body>
</html>
```